Using attached logo that has been created

Business card with logo that's attached. Maybe with water or the cartoon van in background. Looking for it to not be so plain and not too white.
Information to include;
Rodney Ashcombe
(555) 218-7730
Info@bramleypipeworks.example
www.bramleypipeworks.example
License # 4627195
Looking forward to the designs u come up with.
Thank you!
-Delphine
Target Market(s)
Plumbing
Industry/Entity Type
Plumbing
Contact Information for Business Card
Listed above

```html
<!DOCTYPE html>
<html lang="en">
<head>
<meta charset="utf-8">
<title>Bramley Pipeworks – Business Card</title>
<link rel="stylesheet" href="https://fonts.googleapis.com/css2?family=Libre+Baskerville:wght@400;700&display=swap">
<style>
  :root {
    --canvas: #d9d9d9;
    --card-white: #ffffff;
    --brand-blue: #1d4fb0;
    --brand-yellow: #fdbd0a;
    --ink: #3a3a3a;
    --ink-dark: #1b1b1b;
    --art-blue: #2e64c4;
    --art-tan: #9c8560;
  }
  * { box-sizing: border-box; margin: 0; padding: 0; }
  html, body { width: 1200px; height: 800px; overflow: hidden; }
  body {
    background: var(--canvas);
    font-family: "Libre Baskerville", Georgia, serif;
    position: relative;
  }
  .card {
    position: absolute;
    width: 560px;
    height: 320px;
    border-radius: 22px;
    overflow: hidden;
    box-shadow: 0 10px 24px rgba(0,0,0,0.18);
  }
  /* Front */
  .card-front {
    left: 60px; top: 70px;
    background: var(--card-white);
    border-bottom: 12px solid var(--brand-blue);
  }
  .front-mascot {
    position: absolute;
    left: 20px; bottom: 0;
    width: 250px; height: 230px;
    border-radius: 110px 110px 0 0;
    background: linear-gradient(160deg, #c89a7a 0%, var(--art-blue) 40%, var(--art-tan) 85%);
  }
  .front-info {
    position: absolute;
    left: 290px; top: 44px;
    width: 250px;
  }
  .brand-name {
    color: var(--brand-blue);
    font-weight: 700;
    font-size: 25px;
    line-height: 1.15;
    text-transform: uppercase;
    padding-bottom: 10px;
    border-bottom: 3px solid var(--brand-blue);
    margin-bottom: 22px;
  }
  .person-name {
    color: var(--brand-blue);
    font-weight: 700;
    font-size: 17px;
    text-transform: uppercase;
    margin-bottom: 10px;
  }
  .contact-list { list-style: none; font-size: 11.5px; color: var(--ink); line-height: 1.75; }
  .contact-list li { display: flex; align-items: center; gap: 7px; }
  .contact-list svg { width: 11px; height: 11px; fill: var(--brand-blue); flex: none; }
  .contact-list .no-icon { padding-left: 0; }
  /* Back */
  .card-back {
    left: 580px; top: 420px;
    background: var(--brand-yellow);
  }
  .back-mascot {
    position: absolute;
    left: 50%; top: 34px;
    transform: translateX(-50%);
    width: 150px; height: 170px;
    border-radius: 70px 70px 16px 16px;
    background: linear-gradient(170deg, #c89a7a 0%, var(--art-blue) 35%, var(--art-tan) 80%);
  }
  .back-brand {
    position: absolute;
    left: 0; right: 0; top: 208px;
    text-align: center;
    color: var(--brand-blue);
    font-weight: 700;
    font-size: 24px;
    text-transform: uppercase;
  }
  .back-web {
    position: absolute;
    left: 0; right: 0; bottom: 30px;
    text-align: center;
    color: var(--ink-dark);
    font-size: 12px;
    letter-spacing: 5px;
    text-transform: uppercase;
  }
</style>
</head>
<body>
  <section class="card card-front">
    <div class="front-mascot" role="img" aria-label="Cartoon plumber mascot holding a pipe wrench and a circular saw"></div>
    <div class="front-info">
      <h1 class="brand-name">Bramley Pipeworks &amp; More</h1>
      <h2 class="person-name">Rodney Ashcombe</h2>
      <ul class="contact-list">
        <li class="no-icon">License # 4627195</li>
        <li><svg viewBox="0 0 24 24"><path d="M6.6 10.8a15.1 15.1 0 0 0 6.6 6.6l2.2-2.2a1 1 0 0 1 1-.25 11.4 11.4 0 0 0 3.6.57 1 1 0 0 1 1 1V20a1 1 0 0 1-1 1A17 17 0 0 1 3 4a1 1 0 0 1 1-1h3.5a1 1 0 0 1 1 1c0 1.25.2 2.45.57 3.57a1 1 0 0 1-.25 1z"/></svg>(555) 218-7730</li>
        <li><svg viewBox="0 0 24 24"><path d="M2 5h20v14H2z M2 5l10 8 10-8" stroke="#fff" stroke-width="1.5"/></svg>Info@bramleypipeworks.example</li>
        <li><svg viewBox="0 0 24 24"><circle cx="12" cy="12" r="10"/><path d="M2 12h20M12 2c3 3 3 17 0 20M12 2c-3 3-3 17 0 20" stroke="#fff" stroke-width="1.5" fill="none"/></svg>www.bramleypipeworks.example</li>
      </ul>
    </div>
  </section>

  <section class="card card-back">
    <div class="back-mascot" role="img" aria-label="Cartoon plumber mascot holding a pipe wrench and a circular saw"></div>
    <p class="back-brand">Bramley Pipeworks &amp; More</p>
    <p class="back-web">www.bramleypipeworks.example</p>
  </section>
</body>
</html>
```